Direct to Consumer extended service contract business with a new disruptive business model needs a

We need a customized wordpress design for a company called 'Bright Harbor Assurance'.
We provide an innovative and unique service contract protection program direct to consumers. This program provides monthly coverage for all electronics purchased in the last 4 years and all electronics the consumer purchases in the future for a low monthly fee. The overall design should communicate a sense of legitimacy, ethics, and superior customer service and support (in an industry that has a huge PR issue to overcome).
Electronics is the first product group, other product groups with different price points to launch in the future..

Target Market(s)

All purchasers of electronic goods...all demographics

Industry/Entity Type

Electronics

Font styles to use
Sans Serif

Requirements
Must have
• Customer Testimonials
Industry News
Customer ratings
Blog posts
Call to action messaging
Like the functional elements and design of quillmesa.example (need to be better)
Nice to have
• Like to see video testimonials
Social network "whats trending related to electronics or service contract industry"
Easy way to register products for warranty

```html
<!DOCTYPE html>
<html lang="en">
<head>
<meta charset="utf-8">
<title>Bright Harbor Assurance</title>
<link rel="stylesheet" href="https://fonts.googleapis.com/css2?family=Oswald:wght@400;500&family=Lato:wght@400;700&family=Open+Sans:wght@300;400&display=swap">
<style>
:root{
  --orange:#f7901e;
  --orange-dark:#e5761a;
  --ink:#222;
  --dark:#2d2e30;
  --darker:#232426;
  --grey:#6b6b6b;
  --white:#fff;
  --line:#d9dbe0;
}
*{box-sizing:border-box;margin:0;padding:0}
html,body{width:699px;height:1200px;overflow:hidden;background:var(--white)}
body{position:relative;font-family:"Lato",sans-serif;color:var(--ink)}
.abs{position:absolute}
.heading{font-family:"Oswald",sans-serif;font-weight:500;text-transform:uppercase;letter-spacing:-.2px}
.heading em{font-style:normal;color:var(--orange)}

/* top bar */
.topbar{left:0;top:0;width:699px;height:18px;background:var(--dark);color:var(--white);font-size:8px;font-weight:700}
.topbar .tagline{left:78px;top:4px}
.topbar .tagline em{font-style:normal;color:var(--orange)}
.topbar .account{left:434px;top:4px;display:flex;gap:16px;font-weight:400}
.social-mini{left:543px;top:0;display:flex}
.social-mini span{width:16px;height:18px;display:block}
.social-mini span i{display:block;width:6px;height:6px;margin:6px auto;background:#cfd0d2}
.social-mini span.active{background:var(--orange)}
.social-mini span.active i{background:var(--white)}

/* header */
.brand{left:78px;top:28px;display:flex;align-items:center;gap:8px}
.brand .mark{width:20px;height:20px;background:var(--orange)}
.brand .name{font-family:"Lato",sans-serif;font-weight:700;font-size:17px;color:#3a3a3a;line-height:1}
.callout{right:75px;top:29px;font-family:"Oswald",sans-serif;font-size:14px;color:var(--ink)}
.callout span{color:var(--orange);font-size:11px}
.email{right:75px;top:54px;font-size:8px;color:#444;display:flex;gap:5px;align-items:center}

/* nav */
.nav{left:0;top:75px;width:699px;height:27px;background:linear-gradient(var(--orange),var(--orange-dark))}
.nav ul{list-style:none;position:absolute;left:78px;top:0;display:flex;height:27px;align-items:center}
.nav li{font-family:"Lato",sans-serif;font-weight:700;font-size:9.5px;color:#2a2a2a;padding:0 20px;border-left:1px solid rgba(255,255,255,.5);line-height:12px}
.nav li:first-child{background:var(--dark);color:var(--white);font-weight:400;height:30px;line-height:30px;margin-top:-3px;padding:0 13px;border:none}
.nav li:nth-child(2){border-left:none}

/* hero */
.hero{left:0;top:102px;width:699px;height:256px;background:linear-gradient(120deg,#f5f6f8,#e9ebef 50%,#f6f7f9)}
.hero .kicker{left:76px;top:48px;font-family:"Open Sans",sans-serif;font-size:18px;color:#333;font-weight:300}
.hero h1{left:76px;top:74px;font-family:"Open Sans",sans-serif;font-weight:400;font-size:22px;color:#222}
.hero .price{left:76px;top:104px;font-family:"Open Sans",sans-serif;font-size:18px;font-weight:300;color:#222}
.hero .price b{font-weight:400}
.btn-quote{left:77px;top:135px;width:115px;height:26px;background:var(--orange);border-radius:2px;box-shadow:0 2px 0 var(--orange-dark);font-family:"Lato",sans-serif;font-weight:700;font-size:11.5px;color:#2a2a2a;text-align:center;line-height:26px}
.hero .save{left:77px;top:177px;font-family:"Open Sans",sans-serif;font-size:11px;line-height:15.5px;color:#333}
.hero .appliances{left:358px;top:34px;width:326px;height:200px;border-radius:6px;background:linear-gradient(135deg,#dfe2e6 0%,#c8ccd2 45%,#e6e8eb 70%,#f3d2ae 100%)}

/* feature band */
.band-edge{left:0;top:357px;width:699px;height:3px;background:var(--orange)}
.features{left:0;top:360px;width:699px;height:103px;background:var(--dark)}
.feature{top:0;width:137px;height:103px;background:linear-gradient(#3d3e40,#2a2b2d);text-align:center;color:var(--white)}
.feature .tip{position:absolute;left:0;bottom:0;width:137px;height:10px;background:linear-gradient(173deg,transparent 55%,var(--orange) 56%)}
.feature svg{margin-top:11px}
.feature .rule{width:110px;height:1px;background:#555;margin:5px auto 0}
.feature .label{font-family:"Oswald",sans-serif;font-size:11.5px;margin-top:9px;text-transform:uppercase}

/* welcome */
.section-title{left:0;width:699px;text-align:center;font-size:17px}
.section-title:after{content:"";display:block;width:130px;height:1px;margin:6px auto 0;background:var(--line)}
.welcome-text{left:78px;top:528px;width:543px;text-align:center;font-size:7.2px;line-height:14px;color:#333}
.btn-more{left:320px;top:584px;width:59px;height:20px;background:var(--dark);color:var(--white);font-family:"Oswald",sans-serif;font-size:8px;text-align:center;line-height:20px;border-radius:2px;box-shadow:0 2px 0 #111}
.divider{left:95px;width:510px;height:1px;background:linear-gradient(90deg,transparent,#cdd2dc,transparent)}

/* testimonials */
.videos{left:77px;top:694px;width:546px;height:124px;background:var(--white);box-shadow:0 0 12px rgba(0,0,0,.12)}
.video{top:12px;width:158px}
.video .screen{width:140px;height:92px;margin:0 auto;background:#1c1c1c;border-radius:4px 4px 0 0;padding:6px}
.video .clip{width:128px;height:80px;background:linear-gradient(#dcdcdc,#c6c6c6);display:flex;align-items:center;justify-content:center}
.video .base{width:158px;height:5px;background:linear-gradient(#d8d8d8,#a9a9a9);border-radius:0 0 6px 6px}
.video-name{top:815px;width:158px;text-align:center;font-size:8.5px;color:#333}

/* three columns */
.col-title{top:873px;width:190px;text-align:center;font-size:17px}
.col-title:after{content:"";display:block;width:130px;height:1px;margin:5px auto 0;background:var(--line)}
.news{left:78px;width:160px;display:flex;gap:9px}
.date{width:25px;flex:none;text-align:center;color:var(--white)}
.date .m{background:var(--orange);font-size:6.5px;height:9px;line-height:9px}
.date .d{background:#8e8e8e;font-size:11px;height:15px;line-height:15px}
.news h4,.rating h4,.blog h4{font-size:7.5px;font-weight:700;color:#222;margin-bottom:2px}
.news p{font-size:6.8px;line-height:10px;color:#555}
.rating{left:271px;display:flex;gap:14px}
.avatar{width:40px;height:40px;border-radius:50%;background:linear-gradient(#c7b8ad,#8b7a70);flex:none;box-shadow:0 0 0 2px #eee}
.stars{display:flex;gap:4px;margin:4px 0 5px}
.stars span{width:9px;height:9px;background:var(--orange);color:var(--white);font-size:7px;line-height:9px;text-align:center}
.rating p,.blog p{font-size:7.5px;color:#444}
.blog{left:467px;display:flex;gap:12px}
.thumb{width:42px;height:32px;flex:none;border:1px solid #ddd}
.blog i{font-size:7.5px;color:#444;display:block}
.vrule{top:870px;width:1px;height:140px;background:linear-gradient(transparent,#ddd,transparent)}

/* footer */
.footer{left:0;top:1038px;width:699px;height:162px;background:var(--dark);border-top:3px solid var(--orange);color:#ddd}
.footer h5{font-family:"Lato",sans-serif;font-weight:400;font-size:12px;color:var(--white);padding-bottom:5px;border-bottom:1px solid #555;margin-bottom:7px}
.fcol{top:17px}
.fcol p,.fcol li{font-size:7.5px;line-height:11px}
.field{width:125px;height:15px;background:#5a5b5d;margin-top:6px;font-size:7px;line-height:15px;padding-left:5px;color:#eee}
.btn-sub{margin-top:9px;width:52px;height:16px;background:var(--orange);font-size:7.5px;line-height:16px;text-align:center;color:var(--white);font-weight:700}
.contact-row{display:flex;gap:10px;margin-bottom:8px;font-size:7.5px;line-height:11px}
.contact-row svg{flex:none}
.links{list-style:none}
.links li{line-height:14.5px}
.links li:before{content:"› ";color:#aaa}
.follow div{display:flex;align-items:center;gap:12px;font-size:7.5px;margin-bottom:7px}
.follow span{width:16px;height:16px;background:#56708f;display:block}
.copyright{left:0;top:1177px;width:699px;height:23px;background:var(--darker);text-align:center;font-size:7.5px;color:#ccc;line-height:23px}
</style>
</head>
<body>

<div class="abs topbar">
  <div class="abs tagline">We believe in <em>100%</em> customer satisfaction!</div>
  <div class="abs account"><span>Login</span><span>Register</span></div>
  <div class="abs social-mini" aria-label="Social links">
    <span class="active"><i></i></span><span><i></i></span><span><i></i></span><span><i></i></span><span><i></i></span>
  </div>
</div>

<div class="abs brand">
  <span class="mark"></span>
  <span class="name">Bright Harbor Assurance</span>
</div>
<div class="abs callout"><span>Call Us Now : </span>+1-555-014-2200</div>
<div class="abs email">
  <svg width="10" height="7" viewBox="0 0 10 7"><rect x=".5" y=".5" width="9" height="6" fill="none" stroke="#666"/><path d="M.5 .5 5 4 9.5 .5" fill="none" stroke="#666"/></svg>
  hello@brightharbor.example
</div>

<nav class="abs nav">
  <ul><li>Home</li><li>ABOUT US</li><li>SERVICES</li><li>PLANS</li><li>BLOGS</li><li>CONTACT US</li></ul>
</nav>

<section class="abs hero">
  <div class="abs kicker">PROTECT YOUR</div>
  <h1 class="abs">ELECCTRONIC APPLIANCES</h1>
  <div class="abs price">FOR <b>$25</b> A MONTH OR LESS</div>
  <div class="abs btn-quote">GET A QUOTE</div>
  <p class="abs save">Save up to 60% vs<br>your current Electronic insurance</p>
  <div class="abs appliances" role="img" aria-label="Refrigerator, washing machine and desktop computer with an orange accent"></div>
</section>

<div class="abs band-edge"></div>
<section class="abs features">
  <div class="abs feature" style="left:78px">
    <svg width="30" height="30" viewBox="0 0 30 30"><circle cx="15" cy="15" r="13" fill="#f7901e"/><circle cx="15" cy="15" r="8" fill="none" stroke="#2d2e30" stroke-width="2"/><path d="M11 15l3 3 5-6" fill="none" stroke="#2d2e30" stroke-width="2"/></svg>
    <div class="rule"></div><div class="label">Register a Plan</div><div class="tip"></div>
  </div>
  <div class="abs feature" style="left:215px">
    <svg width="30" height="30" viewBox="0 0 30 30"><rect x="6" y="4" width="16" height="22" fill="none" stroke="#f7901e" stroke-width="2"/><path d="M9 10h10M9 14h10M9 18h6" stroke="#f7901e" stroke-width="1.5"/><circle cx="22" cy="22" r="5" fill="#f7901e"/><path d="M20 22l1.5 1.5 3-3" fill="none" stroke="#fff" stroke-width="1.2"/></svg>
    <div class="rule"></div><div class="label">File a Claim</div><div class="tip"></div>
  </div>
  <div class="abs feature" style="left:352px">
    <svg width="30" height="30" viewBox="0 0 30 30"><circle cx="15" cy="11" r="6" fill="#f7901e"/><path d="M6 27c0-7 4-9 9-9s9 2 9 9z" fill="#f7901e"/><path d="M8 11a7 7 0 0 1 14 0" fill="none" stroke="#f7901e" stroke-width="1.5"/></svg>
    <div class="rule"></div><div class="label">Support</div><div class="tip"></div>
  </div>
  <div class="abs feature" style="left:489px">
    <svg width="30" height="30" viewBox="0 0 30 30"><circle cx="11" cy="12" r="7" fill="none" stroke="#f7901e" stroke-width="3.5" stroke-dasharray="3 2"/><circle cx="22" cy="22" r="4.5" fill="none" stroke="#f7901e" stroke-width="3" stroke-dasharray="2.5 1.5"/></svg>
    <div class="rule"></div><div class="label">Services</div><div class="tip"></div>
  </div>
</section>

<h2 class="abs heading section-title" style="top:481px">Welcome <em>Bright Harbor</em></h2>
<p class="abs welcome-text">Lorem ipsum dolor sit amet, consectetuer adipiscing elit, sed diam nonummy nibh euismod tincidunt ut laoreet dolore magna aliquam erat volutpat. Ut wisi enim ad minim veniam, quis nostrud exerci tation ullamcorper suscipit lobortis nisl ut aliquip commodo consequat. Duis autem vel eum iriure dolor in he vulputate velit esse molestie consequat, vel illum dolore eu feugiat nulla facilisis at vero eros et accumsan et iusto odio dignissimaug</p>
<div class="abs btn-more">READ MORE</div>

<div class="abs divider" style="top:622px"></div>
<h2 class="abs heading section-title" style="top:640px">Our <em>Client Says</em></h2>

<section class="abs videos">
  <div class="abs video" style="left:0">
    <div class="screen"><div class="clip" role="img" aria-label="Video testimonial of a male customer"><svg width="22" height="22" viewBox="0 0 22 22"><circle cx="11" cy="11" r="11" fill="#f7901e"/><path d="M9 6.5v9l7-4.5z" fill="#fff"/></svg></div></div>
    <div class="base"></div>
  </div>
  <div class="abs video" style="left:194px">
    <div class="screen"><div class="clip" role="img" aria-label="Video testimonial of a female customer"><svg width="22" height="22" viewBox="0 0 22 22"><circle cx="11" cy="11" r="11" fill="#f7901e"/><path d="M9 6.5v9l7-4.5z" fill="#fff"/></svg></div></div>
    <div class="base"></div>
  </div>
  <div class="abs video" style="left:388px">
    <div class="screen"><div class="clip" role="img" aria-label="Video testimonial of a business customer"><svg width="22" height="22" viewBox="0 0 22 22"><circle cx="11" cy="11" r="11" fill="#f7901e"/><path d="M9 6.5v9l7-4.5z" fill="#fff"/></svg></div></div>
    <div class="base"></div>
  </div>
</section>
<div class="abs video-name" style="left:77px">Mr. Alden Marsh</div>
<div class="abs video-name" style="left:271px">Miss Coral Fenwick</div>
<div class="abs video-name" style="left:465px">Rowan, Brightlane Works, USA</div>

<div class="abs divider" style="top:847px"></div>

<h3 class="abs heading col-title" style="left:65px">Latest <em>News</em></h3>
<h3 class="abs heading col-title" style="left:258px">Customer <em>Ratings</em></h3>
<h3 class="abs heading col-title" style="left:448px">Recent <em>Blog</em></h3>
<div class="abs vrule" style="left:251px"></div>
<div class="abs vrule" style="left:445px"></div>

<div class="abs news" style="top:915px">
  <div class="date"><div class="m">AUG</div><div class="d">10</div></div>
  <div><h4>Lorem ipsum dolor sit amet .</h4><p>Lorem ipsum dol adipiscing elit, seder or sit amet., consectetuer adipiscing</p></div>
</div>
<div class="abs news" style="top:968px">
  <div class="date"><div class="m">AUG</div><div class="d">11</div></div>
  <div><h4>Lorem ipsum dolor sit amet .</h4><p>Lorem ipsum dol adipiscing elit, seder or sit amet., consectetuer adipiscing</p></div>
</div>

<div class="abs rating" style="top:910px">
  <div class="avatar" role="img" aria-label="Customer portrait"></div>
  <div><h4>Conse Ctetuer</h4><div class="stars"><span>★</span><span>★</span><span>★</span></div><p>Utwisi enim ad m venialj quisa</p></div>
</div>
<div class="abs rating" style="top:966px">
  <div class="avatar" role="img" aria-label="Customer couple portrait"></div>
  <div><h4>Adipiscing Elit</h4><div class="stars"><span>★</span><span>★</span><span>★</span><span>★</span><span>★</span></div><p>Utwisi enim ad m venialj quisa</p></div>
</div>

<div class="abs blog" style="top:910px">
  <div class="thumb" role="img" aria-label="Blog thumbnail: desk pendulum" style="background:linear-gradient(#f4f4f4,#cfd3d8)"></div>
  <div><h4>Lorem ipsum dolor sit amet</h4><i>AUG 9, 2014</i><p>Utwisi enim ad m venialj quisa</p></div>
</div>
<div class="abs blog" style="top:965px">
  <div class="thumb" role="img" aria-label="Blog thumbnail: life buoy" style="background:linear-gradient(#d9a39c,#b7463b)"></div>
  <div><h4>Lorem ipsum dolor sit amet</h4><i>AUG 25, 2014</i><p>Utwisi enim ad m venialj quisa</p></div>
</div>

<footer class="abs footer">
  <div class="abs fcol" style="left:78px;width:125px">
    <h5>Newsletter</h5>
    <p>Signup with us and get update in your inbox.</p>
    <div class="field">Your Name</div>
    <div class="field">Email address</div>
    <div class="btn-sub">SUBSCRIBE</div>
  </div>
  <div class="abs fcol" style="left:245px;width:112px">
    <h5>Contact Us</h5>
    <div class="contact-row"><svg width="9" height="12" viewBox="0 0 9 12"><path d="M4.5 0A4.5 4.5 0 0 0 0 4.5C0 8 4.5 12 4.5 12S9 8 9 4.5A4.5 4.5 0 0 0 4.5 0z" fill="#fff"/><circle cx="4.5" cy="4.5" r="1.6" fill="#2d2e30"/></svg><span>Lorem ipsum dolor sit nil amet, consectetuer adipiscing elit, sed diam</span></div>
    <div class="contact-row"><svg width="9" height="11" viewBox="0 0 9 11"><rect x="1" y=".5" width="7" height="10" rx="1" fill="none" stroke="#fff"/><path d="M3 8.5h3" stroke="#fff"/></svg><span>+1-555-014-2201</span></div>
    <div class="contact-row"><svg width="11" height="9" viewBox="0 0 11 9"><rect x=".5" y=".5" width="10" height="8" fill="none" stroke="#fff"/><path d="M.5 .5 5.5 5l5-4.5" fill="none" stroke="#fff"/></svg><span>hello@brightharbor.example</span></div>
  </div>
  <div class="abs fcol" style="left:399px;width:110px">
    <h5>Quick Links</h5>
    <ul class="links"><li>Home</li><li>About Us</li><li>Services</li><li>Plans</li><li>Testimonials</li><li>Contact Us</li></ul>
  </div>
  <div class="abs fcol follow" style="left:548px;width:75px">
    <h5 style="border:none">Follow Us On</h5>
    <div><span></span>Friendloop</div>
    <div><span></span>Chirpline</div>
    <div><span></span>Viewcast</div>
    <div><span></span>Workgrid</div>
  </div>
</footer>
<div class="abs copyright">© Copyright 2014 Bright Harbor Assurance. All Rights Reserved</div>

</body>
</html>
```